Landing Page / Waitlist

I would like a landing page for people to sign up for a waiting list. The text on the page should include (but is not limited to):
1) Main point: The accounting system you'll love
2) Secondary points:
a. Ruthlessly efficient
b. Quietly intelligent
c. Driven by AI
I've attached a file of our logo

The design should be simple, clean, and innovative - this is an ai company

```html
<!DOCTYPE html>
<html lang="en">
<head>
<meta charset="UTF-8">
<title>TallyBright – Join the Waitlist</title>
<link href="https://fonts.googleapis.com/css2?family=Montserrat:wght@700&family=Lato:wght@400&display=swap" rel="stylesheet">
<style>
  :root {
    --bg-deep: #0a4f86;
    --bg-mid: #1477b3;
    --bg-light: #2a9fd0;
    --bg-teal: #3fb0c8;
    --card: #ffffff;
    --ink: #0b0b0b;
    --ink-soft: #3d3d3d;
    --brand-grey: #7b7b7b;
    --brand-blue: #0a9cf2;
    --field-border: #8e8e8e;
    --btn-top: #10b8ff;
    --btn-bottom: #0a8cef;
    --btn-text: #ffffff;
  }
  * { box-sizing: border-box; margin: 0; padding: 0; }
  html, body {
    width: 1200px;
    height: 600px;
    overflow: hidden;
  }
  body {
    position: relative;
    font-family: "Lato", sans-serif;
    background: var(--bg-deep);
  }
  .backdrop {
    position: absolute;
    inset: 0;
    background:
      radial-gradient(ellipse 500px 300px at 15% 85%, rgba(63,176,200,0.55), transparent 70%),
      radial-gradient(ellipse 420px 320px at 88% 30%, rgba(42,159,208,0.45), transparent 70%),
      linear-gradient(160deg, var(--bg-deep) 0%, var(--bg-mid) 55%, var(--bg-light) 100%);
  }
  .waitlist-card {
    position: absolute;
    left: 263px;
    top: 74px;
    width: 674px;
    height: 452px;
    background: var(--card);
    border-radius: 22px;
    text-align: center;
  }
  .brand {
    position: absolute;
    left: 0;
    right: 0;
    top: 66px;
    height: 60px;
    display: flex;
    justify-content: center;
    align-items: center;
    gap: 14px;
  }
  .brand-mark {
    width: 40px;
    height: 40px;
    background: var(--brand-blue);
  }
  .brand-name {
    font-family: "Lato", sans-serif;
    font-weight: 400;
    font-size: 44px;
    color: var(--brand-grey);
    line-height: 1;
  }
  .headline {
    position: absolute;
    left: 0;
    right: 0;
    top: 150px;
    font-family: "Montserrat", sans-serif;
    font-weight: 700;
    font-size: 37px;
    line-height: 43px;
    color: var(--ink);
  }
  .tagline {
    position: absolute;
    left: 0;
    right: 0;
    top: 249px;
    font-size: 21.5px;
    line-height: 26px;
    color: var(--ink-soft);
  }
  .signup-form {
    position: absolute;
    left: 65px;
    top: 302px;
    width: 544px;
    height: 60px;
    border: 1px solid var(--field-border);
    border-radius: 30px;
    display: flex;
    align-items: center;
    padding: 0 3px 0 20px;
  }
  .email-field {
    flex: 1;
    border: none;
    outline: none;
    background: transparent;
    font-family: "Lato", sans-serif;
    font-size: 19px;
    color: var(--ink-soft);
  }
  .email-field::placeholder { color: var(--ink-soft); }
  .join-button {
    width: 214px;
    height: 52px;
    border: none;
    border-radius: 26px;
    background: linear-gradient(180deg, var(--btn-top), var(--btn-bottom));
    color: var(--btn-text);
    font-family: "Lato", sans-serif;
    font-size: 22px;
    cursor: pointer;
  }
  .copyright {
    position: absolute;
    left: 0;
    right: 0;
    top: 405px;
    font-size: 15.5px;
    line-height: 20px;
    color: var(--ink-soft);
  }
</style>
</head>
<body>
  <div class="backdrop" role="img" aria-label="Blurred blue photograph of financial line charts and candlestick graphs"></div>

  <main class="waitlist-card">
    <div class="brand">
      <span class="brand-mark"></span>
      <span class="brand-name">TallyBright</span>
    </div>

    <h1 class="headline">The Accounting System<br>You'll Love</h1>
    <p class="tagline">Ruthlessly efficient. Quietly intelligent. Driven by AI.</p>

    <form class="signup-form" action="#">
      <input class="email-field" type="email" placeholder="Email" aria-label="Email">
      <button class="join-button" type="submit">Join the Waitlist</button>
    </form>

    <p class="copyright">Copyright © 2025 TallyBright. All rights reserved.</p>
  </main>
</body>
</html>
```